GJ & DW Fencing Pty Ltd

We already have an existing logo created by Pixel Harbour however we have restructured to a company. We would like someone to add Pty Ltd to our business name please.

Colors

Designer to choose only greyscale colors for use in the design.

```html
<!DOCTYPE html>
<html lang="en">
<head>
<meta charset="utf-8">
<title>GJ &amp; DW Fencing Pty Ltd – Business Card</title>
<link rel="stylesheet" href="https://fonts.googleapis.com/css2?family=Lato:wght@400&family=Merriweather:wght@900&display=swap">
<style>
  :root {
    --backdrop: #2b2b2d;
    --backdrop-edge: #1c1c1e;
    --card: #0c0c0c;
    --card-sheen: #1a1a1a;
    --ink: #ffffff;
    --ink-soft: #d9d9d9;
    --rule: #6a6a6a;
    --silver: #e6e6e6;
  }
  * { margin: 0; padding: 0; box-sizing: border-box; }
  html, body { width: 1200px; height: 900px; overflow: hidden; }
  body {
    background: radial-gradient(ellipse at 45% 40%, var(--backdrop) 0%, var(--backdrop-edge) 100%);
    position: relative;
    font-family: "Lato", sans-serif;
  }
  .card {
    position: absolute;
    left: 340px;
    width: 520px;
    height: 300px;
    background: linear-gradient(160deg, var(--card-sheen) 0%, var(--card) 60%);
    box-shadow: 0 14px 30px rgba(0,0,0,.55);
    overflow: hidden;
  }
  .card::after {
    content: "";
    position: absolute;
    left: 0; right: 0; bottom: 0;
    height: 4px;
    background: linear-gradient(90deg, transparent 0%, var(--silver) 50%, transparent 100%);
  }
  .card--front { top: 110px; }
  .card--back { top: 470px; }

  .brand {
    position: absolute;
    inset: 0;
    display: flex;
    align-items: center;
    justify-content: center;
    gap: 14px;
  }
  .brand__mark {
    width: 34px; height: 34px;
    border-radius: 50%;
    background: var(--ink);
  }
  .brand__name {
    font-family: "Merriweather", serif;
    font-weight: 900;
    color: var(--ink);
    font-size: 30px;
    line-height: 1.1;
    letter-spacing: .5px;
  }
  .brand__name span { display: block; font-size: 22px; letter-spacing: 2px; }

  .contact {
    position: absolute;
    inset: 0;
    display: flex;
    flex-direction: column;
    align-items: center;
    justify-content: center;
    color: var(--ink-soft);
  }
  .contact__name {
    font-family: "Merriweather", serif;
    font-weight: 900;
    color: var(--ink);
    font-size: 19px;
    letter-spacing: 1px;
    margin-bottom: 14px;
  }
  .contact__divider {
    display: flex;
    align-items: center;
    width: 150px;
    gap: 8px;
  }
  .contact__divider::before,
  .contact__divider::after {
    content: "";
    flex: 1;
    height: 1px;
    background: var(--rule);
  }
  .contact__icon {
    width: 24px; height: 24px;
    border-radius: 50%;
    background: var(--ink);
    display: flex; align-items: center; justify-content: center;
  }
  .contact__line {
    font-size: 18px;
    margin: 2px 0 4px;
    letter-spacing: .3px;
  }
</style>
</head>
<body>
  <section class="card card--front" aria-label="Card front">
    <div class="brand">
      <div class="brand__mark"></div>
      <div class="brand__name">GJ &amp; DW<span>FENCING PTY LTD</span></div>
    </div>
  </section>

  <section class="card card--back" aria-label="Card back">
    <div class="contact">
      <h1 class="contact__name">DALE WHITCOMBE</h1>

      <div class="contact__divider">
        <span class="contact__icon">
          <svg width="14" height="14" viewBox="0 0 24 24" aria-hidden="true"><path fill="#0c0c0c" d="M6.6 10.8a15.1 15.1 0 0 0 6.6 6.6l2.2-2.2c.3-.3.7-.4 1-.2 1.1.4 2.3.6 3.6.6.6 0 1 .4 1 1V20c0 .6-.4 1-1 1A17 17 0 0 1 3 4c0-.6.4-1 1-1h3.5c.6 0 1 .4 1 1 0 1.3.2 2.5.6 3.6.1.3 0 .7-.2 1z"/></svg>
        </span>
      </div>
      <p class="contact__line">044 5120947</p>

      <div class="contact__divider">
        <span class="contact__icon">
          <svg width="14" height="14" viewBox="0 0 24 24" aria-hidden="true"><rect x="3" y="6" width="18" height="12" rx="1" fill="#0c0c0c"/><path d="M3.5 6.5 12 13l8.5-6.5" stroke="#fff" stroke-width="1.5" fill="none"/></svg>
        </span>
      </div>
      <p class="contact__line">office@gjdwfencing.com.au</p>

      <div class="contact__divider">
        <span class="contact__icon">
          <svg width="14" height="14" viewBox="0 0 24 24" aria-hidden="true"><path fill="#0c0c0c" d="M12 2a7 7 0 0 0-7 7c0 5.2 7 13 7 13s7-7.8 7-13a7 7 0 0 0-7-7zm0 9.5A2.5 2.5 0 1 1 12 6.5a2.5 2.5 0 0 1 0 5z"/></svg>
        </span>
      </div>
      <p class="contact__line">PO Box 418 Greenvale WA 6510</p>
    </div>
  </section>
</body>
</html>
```